Profesional personal website needs design and business card

I need a business card with my professional name as a logo "Dorian Vitality" for my business. I am a Wellness Coach, consultant and trainer. So it should be professional, wellness oriented and modern.

Target Market(s)

Private clients, governments, corporations. Luxury and high market.

Industry/Entity Type

Health And Wellness

Contact Information for Business Card

Dorian Vitality should be the logo

Colors

Designer to choose colors to be used in the design.

Requirements
Must have
• Dorian Vitality
• Name: Tomás Lirandel
• Wellness Coach, Consultant & Trainer.
• Website: www.dorianvitality-example.com
• Phone:
• Spain (+34) 612 480 317
• (USA) +1 (555) 610 4829
Nice to have
• The most important is the design of "Dorian Vitality", as this is going to be my personal brand logo. It should be professional, wellness, high end and actual.
Should not have
• no golds, no baroque style..

```html
<!DOCTYPE html>
<html lang="en">
<head>
<meta charset="utf-8">
<title>Dorian Vitality — Business Card</title>
<link rel="stylesheet" href="https://fonts.googleapis.com/css2?family=Montserrat:wght@400;700&display=swap">
<style>
  :root {
    --ink: #333333;
    --green: #6fc244;
    --paper: #ffffff;
    --stage: #f2f2f0;
    --edge: #4a4a4a;
  }
  * { margin: 0; padding: 0; box-sizing: border-box; }
  html, body {
    width: 1200px; height: 1200px; overflow: hidden;
    background: var(--stage);
    font-family: "Montserrat", Arial, sans-serif;
  }
  .card {
    position: absolute; left: 170px;
    width: 860px; height: 558px;
    border-radius: 40px; overflow: hidden;
  }
  /* Back face */
  .card-back { top: 30px; background: var(--ink); }
  .card-back .corner { position: absolute; inset: 0; }
  .card-back .brand {
    position: absolute; left: 0; right: 0; top: 235px;
    text-align: center; color: var(--paper);
    font-size: 54px; font-weight: 400; letter-spacing: 2px;
  }
  /* Front face */
  .card-front { top: 612px; background: var(--paper); border: 2px solid var(--edge); }
  .tab { position: absolute; top: 153px; height: 241px; width: 44px; }
  .tab-left { left: 0; background: var(--ink); border-radius: 0 44px 44px 0; }
  .tab-right { right: 0; background: var(--green); border-radius: 44px 0 0 44px; }
  .front-brand {
    position: absolute; left: 130px; width: 240px; top: 250px;
    text-align: center; color: var(--green);
    font-size: 28px; font-weight: 400; letter-spacing: 1px;
  }
  .divider { position: absolute; left: 430px; width: 4px; }
  .divider-top { top: 154px; height: 122px; background: var(--ink); }
  .divider-bottom { top: 276px; height: 118px; background: var(--green); }
  .details { position: absolute; left: 447px; top: 152px; color: var(--ink); }
  .name { font-size: 33px; font-weight: 700; line-height: 40px; }
  .role { font-size: 22px; font-weight: 400; line-height: 35px; }
  .contacts { margin-top: 26px; font-size: 22px; line-height: 44px; }
</style>
</head>
<body>
  <div class="card card-back">
    <svg class="corner" width="860" height="558" viewBox="0 0 860 558" aria-hidden="true">
      <polygon points="730,0 860,0 860,300" fill="var(--green)"/>
    </svg>
    <div class="brand">Dorian Vitality</div>
  </div>

  <div class="card card-front">
    <div class="tab tab-left"></div>
    <div class="tab tab-right"></div>
    <div class="front-brand">Dorian Vitality</div>
    <div class="divider divider-top"></div>
    <div class="divider divider-bottom"></div>
    <div class="details">
      <div class="name">Tomás Lirandel</div>
      <div class="role">Wellness Coach</div>
      <div class="role">Consultant &amp; Trainer</div>
      <div class="contacts">
        <div>Spain (+34) 612 480 317</div>
        <div>USA +1 (555) 610 4829</div>
        <div>www.dorianvitality-example.com</div>
      </div>
    </div>
  </div>
</body>
</html>
```